Business Card Design Project

We need a business card for our new business based in Vancouver called
"Korvi" We are looking for a simple yet bold design for our business cards that will enable us to stand out from the pack. All business card details will be provided in the handover stage.
Updates

Thank you to all who have submitted

The work is great for the most part
Cards with creative use of the logo
have been more successful so far

Dark cards and rounded edges 
are also getting good reviews

Double sided is an option we would like to see explored

Thank you

Target Market(s)

Our clients are stressed business people, yoga/meditation enthusiast, and people looking for a new experience in a Spa enviroment

Industry/Entity Type

Business

Font styles to use
Other font styles liked:
• please check design file

Requirements
Must have
• Korvi

5217 E Halden Row, Vancouver, BC V5N 4K7

korvi@calmhaus.ca
Nice to have
• Creative approach to layout and design

Outside of the box design elements
Should not have
• Should not be too busy

```html
<!DOCTYPE html>
<html lang="en">
<head>
<meta charset="utf-8">
<title>Korvi – Business Card</title>
<link rel="stylesheet" href="https://fonts.googleapis.com/css2?family=Josefin+Sans:wght@300;400&display=swap">
<style>
  :root {
    --page-bg: #ffffff;
    --card-bg: #f1f1f3;
    --card-bg-soft: #e3e3e8;
    --frame-blue: #2e37a0;
    --frame-silver: #c9c9cf;
    --brand-blue: #3a3f9c;
    --ink: #2b2b2b;
    --muted: #555555;
  }
  * { box-sizing: border-box; margin: 0; padding: 0; }
  html, body {
    width: 1200px;
    height: 900px;
    overflow: hidden;
    background: var(--page-bg);
  }
  .canvas {
    position: relative;
    width: 1200px;
    height: 900px;
  }
  .card {
    position: absolute;
    left: 103px;
    top: 75px;
    width: 994px;
    height: 580px;
    background: var(--card-bg);
    font-family: "Josefin Sans", sans-serif;
    overflow: hidden;
  }
  .card__texture {
    position: absolute;
    inset: 0;
    background: radial-gradient(ellipse at center, var(--card-bg) 0%, var(--card-bg-soft) 100%);
  }
  .card__frame {
    position: absolute;
    inset: 11px;
    padding: 13px;
    background: linear-gradient(90deg, var(--frame-blue) 0%, var(--frame-blue) 30%, var(--frame-silver) 70%, var(--frame-blue) 100%);
    -webkit-mask: linear-gradient(#000 0 0) content-box, linear-gradient(#000 0 0);
    -webkit-mask-composite: xor;
    mask: linear-gradient(#000 0 0) content-box exclude, linear-gradient(#000 0 0);
  }
  .holder {
    position: absolute;
    right: 47px;
    top: 42px;
    text-align: right;
  }
  .holder__name {
    font-size: 30px;
    font-weight: 400;
    color: var(--frame-blue);
    line-height: 1.1;
  }
  .holder__role {
    font-size: 21px;
    font-weight: 300;
    color: var(--muted);
    line-height: 1.2;
  }
  .brand {
    position: absolute;
    left: 0;
    right: 0;
    top: 160px;
    display: flex;
    align-items: center;
    justify-content: center;
    gap: 40px;
  }
  .brand__dot {
    width: 110px;
    height: 110px;
    border-radius: 50%;
    background: var(--brand-blue);
  }
  .brand__name {
    font-size: 120px;
    font-weight: 300;
    color: var(--brand-blue);
    letter-spacing: 4px;
    line-height: 1;
  }
  .contact {
    position: absolute;
    left: 0;
    right: 0;
    top: 390px;
    text-align: center;
    font-size: 31px;
    font-weight: 300;
    font-style: normal;
    color: var(--ink);
    line-height: 37px;
  }
</style>
</head>
<body>
  <main class="canvas">
    <section class="card">
      <div class="card__texture" role="img" aria-label="Light grey diamond lattice background pattern"></div>
      <div class="card__frame"></div>

      <div class="holder">
        <p class="holder__name">Dara Lindqvist</p>
        <p class="holder__role">Manager</p>
      </div>

      <div class="brand">
        <span class="brand__dot"></span>
        <span class="brand__name">Korvi</span>
      </div>

      <address class="contact">
        <p class="contact__phone">7421 630 918</p>
        <p class="contact__web">www.calmhaus.ca</p>
        <p class="contact__email">korvi@calmhaus.ca</p>
        <p class="contact__address">5217 E Halden Row, Vancouver, BC V5N 4K7</p>
      </address>
    </section>
  </main>
</body>
</html>
```